Business card for law firm

Need business card for new law firm. Think confident, authoritative, conservative, but not stuffy or old-fashioned.

Contact Information for Business Card

Content for card - logo (uploaded), plus the following:

Paul Whitcombe (larger font)
Managing Partner (larger font, but not as large as name)
Level 9, 7 Ferris Lane
Sydney NSW 2000
Main Tel 02 9364 2710
Direct Tel 02 8472 3159
Email paul@qvlegal.com.au
www.qvlegal.com.au

Letterhead design should include logo plus:
Level 9, 7 Ferris Lane
Sydney NSW 2000
Tel 02 8472 3159
www.qvlegal.com.au

```html
<!DOCTYPE html>
<html lang="en">
<head>
<meta charset="utf-8">
<title>QV Legal — Business Card</title>
<link href="https://fonts.googleapis.com/css2?family=Cinzel:wght@400;600&family=Open+Sans:wght@400&display=swap" rel="stylesheet">
<style>
  :root {
    --backdrop: #1d1d1f;
    --card-white: #ffffff;
    --card-black: #050505;
    --ink: #1a1a1a;
    --navy: #1b2a5e;
    --rule: #d4d4d4;
    --paper-text: #f2f2f2;
  }
  * { margin: 0; padding: 0; box-sizing: border-box; }
  html, body {
    width: 1200px; height: 960px; overflow: hidden;
    background: var(--backdrop);
  }
  .canvas {
    width: 1200px; height: 960px;
    display: flex; flex-direction: column;
    align-items: center; justify-content: center; gap: 40px;
  }
  .card {
    width: 720px; height: 411px;
    position: relative;
    box-shadow: 0 10px 30px rgba(0,0,0,.45);
  }

  /* Back side */
  .card-back {
    background: var(--card-black);
    display: flex; flex-direction: column;
    align-items: center; justify-content: center;
  }
  .back-brand {
    display: flex; align-items: center; gap: 22px;
    margin-top: 10px;
  }
  .back-brand .brand-square {
    width: 46px; height: 46px; background: var(--paper-text);
  }
  .back-brand .brand-name {
    font-family: "Cinzel", serif; font-weight: 400;
    font-size: 64px; color: var(--paper-text); letter-spacing: 4px;
  }
  .back-url {
    margin-top: 70px;
    font-family: "Open Sans", sans-serif; font-size: 15px;
    letter-spacing: 4px; color: var(--paper-text);
  }

  /* Front side */
  .card-front {
    background: var(--card-white);
    display: grid; grid-template-columns: 375px 1px 1fr;
    align-items: center;
  }
  .front-brand {
    display: flex; flex-direction: column; align-items: center; gap: 18px;
  }
  .front-brand .brand-square {
    width: 42px; height: 42px; background: var(--navy);
  }
  .front-brand .brand-name {
    font-family: "Cinzel", serif; font-weight: 400;
    font-size: 50px; color: var(--ink); letter-spacing: 3px;
  }
  .divider {
    width: 1px; height: 240px; background: var(--rule);
  }
  .contact {
    padding-left: 26px;
    font-family: "Open Sans", sans-serif; color: var(--ink);
  }
  .contact-name {
    font-family: "Cinzel", serif; font-weight: 600;
    font-size: 22px; color: var(--navy); letter-spacing: .5px;
  }
  .contact-role {
    font-family: "Cinzel", serif; font-weight: 400;
    font-size: 17px; color: var(--ink); letter-spacing: .5px;
    margin-bottom: 6px;
  }
  .contact-address { font-size: 15px; line-height: 1.4; margin-bottom: 6px; }
  .contact-list { list-style: none; font-size: 15px; line-height: 1.5; }
  .contact-list li { display: flex; align-items: center; gap: 8px; }
  .contact-list svg { width: 13px; height: 13px; flex: none; }
  .domain { color: var(--navy); }
</style>
</head>
<body>
<main class="canvas">
  <section class="card card-back" aria-label="Card back">
    <div class="back-brand">
      <span class="brand-square"></span>
      <span class="brand-name">QV Legal</span>
    </div>
    <p class="back-url">www.qvlegal.com.au</p>
  </section>

  <section class="card card-front" aria-label="Card front">
    <div class="front-brand">
      <span class="brand-square"></span>
      <span class="brand-name">QV Legal</span>
    </div>
    <div class="divider"></div>
    <div class="contact">
      <h1 class="contact-name">Paul Whitcombe</h1>
      <h2 class="contact-role">Managing Partner</h2>
      <p class="contact-address">Level 9, 7 Ferris Lane<br>Sydney NSW 2000</p>
      <ul class="contact-list">
        <li>
          <svg viewBox="0 0 16 16" aria-hidden="true"><circle cx="8" cy="8" r="8" fill="#1b2a5e"/><path d="M5 4.2l1.6-.4.9 2.2-1 .8c.5 1.2 1.4 2.1 2.6 2.6l.8-1 2.2.9-.4 1.6c-3.6.2-6.9-3.1-6.7-6.7z" fill="#fff"/></svg>
          02 9364 2710
        </li>
        <li>
          <svg viewBox="0 0 16 16" aria-hidden="true"><circle cx="8" cy="8" r="8" fill="#1b2a5e"/><path d="M5 4.2l1.6-.4.9 2.2-1 .8c.5 1.2 1.4 2.1 2.6 2.6l.8-1 2.2.9-.4 1.6c-3.6.2-6.9-3.1-6.7-6.7z" fill="#fff"/></svg>
          02 8472 3159
        </li>
        <li>
          <svg viewBox="0 0 16 16" aria-hidden="true"><circle cx="8" cy="8" r="8" fill="#1b2a5e"/><rect x="4" y="5.2" width="8" height="5.6" fill="#fff"/><path d="M4 5.2l4 3 4-3" fill="none" stroke="#1b2a5e" stroke-width="1"/></svg>
          paul@qvlegal.com.au
        </li>
        <li>
          <svg viewBox="0 0 16 16" aria-hidden="true"><circle cx="8" cy="8" r="8" fill="#1b2a5e"/><circle cx="8" cy="8" r="4.2" fill="none" stroke="#fff" stroke-width="1"/><ellipse cx="8" cy="8" rx="1.8" ry="4.2" fill="none" stroke="#fff" stroke-width="1"/><path d="M3.8 8h8.4" stroke="#fff" stroke-width="1"/></svg>
          www.<span class="domain">qvlegal</span>.com.au
        </li>
      </ul>
    </div>
  </section>
</main>
</body>
</html>
```